Security and Technology Website - Bold and Confident, Something Unexpected

Maple Wren Systems is launching its first website and we need a great design to bring our brand to life and generate DTC and B2B leads.

We have a good logo, but I am struggling with the creative vision to bring it all together. While our industry is Alarm Systems and Technology, we want to create a site that is more friendly and less 'typical' than your standard IT sites.

It Must:
1. Appeal to both men and women. The logo is a bit masculine, so the colors and icons must soften this.
2. Feel modern - we need to convey that we we use the latest technology.
3. Feel a bit high-end. We are not a budget solution.
4. Have a distinct iconography and photo treatment.
5. Feel layered - not just a series of stacked horizontal modules.

It Should Not:
1. Feel like your typical IT website.

Here are resources to get you started!
• Staging Site:
https://maple-wren-systems.shopfrontdemo.example/
Password: Piper

•Brand Guide: https://www.layoutboard.example/design/QKRmWpLcT4V/hNbq8Yf2-ZsKeRtDw7xp-QE/edit?utm_content=QKRmWpLcT4V&utm_campaign=designshare&utm_medium=link2&utm_source=sharebutton

• Logo and Fonts and Photos: :https://files.cloudlocker.example/folders/7HtPqWmZc3Kd9RbLx2VnYs8FgJe4UoAiT?usp=sharing

• Design Inspiration (don't feel limited by this): https://www.layoutboard.example/design/QKTnHsVbWe8/p7MfRz31xYqLcKdTu9GNBw/edit?utm_content=QKTnHsVbWe8&utm_campaign=designshare&utm_medium=link2&utm_source=sharebutton

______________

The winner will be asked to provide design files and finished PNGs of the overall design file, backgrounds, photo treatments/frames, and icons.

The winner will likely be engaged for a phase 2 to build out a product page.

Industry/Entity Type

Alarm Systems, Home Theatres, and Commercial IT Networking

Number of Pages Required

1 page

Font styles to use
Sans Serif

Colors
0054AA
0677BA
7BADD7
CADEEF
E8F1F8
0094D4
00A9DD
6FCCEA
C7EBF8
E9F6FB
EB3D1F
EC4F4E
F09395
F8D3D4
FCEDEE

Requirements
Must have
• 1. Appeal to both men and women. The logo is a bit masculine, so the colors and icons must soften this. 2. Feel modern - we need to convey that we we use the latest technology. 3. Feel a bit high-end. We are not a budget solution. 4. Have a distinct iconography and photo treatment. 5. Feel layered - not just a series of stacked horizontal modules.
Should not have
• 1. Should not feel like just another IT website.

```html
<!DOCTYPE html>
<html lang="en">
<head>
<meta charset="utf-8">
<title>Maple Wren Systems — Advanced Security Solutions</title>
<link rel="stylesheet" href="https://fonts.googleapis.com/css2?family=Lexend:wght@400;500;600&family=Open+Sans:wght@400;600&display=swap">
<style>
:root{
  --red:#D92A1C;
  --blue:#0677BA;
  --blue-bright:#1A73D1;
  --navy:#0B4F94;
  --navy-card:#0E63B4;
  --footer:#1F5A9E;
  --ink:#2B2B2B;
  --muted:#6A6A6A;
  --ice:#DDF0F7;
  --panel:#F4F4F4;
  --white:#FFFFFF;
}
*{box-sizing:border-box;margin:0;padding:0}
html,body{width:1200px;height:4414px;overflow:hidden}
body{position:relative;background:var(--white);font-family:"Open Sans",sans-serif;color:var(--ink)}
.abs{position:absolute}
.display{font-family:"Lexend",sans-serif;text-transform:uppercase}
.btn{position:absolute;background:var(--red);color:var(--white);font-family:"Lexend",sans-serif;text-transform:uppercase;font-size:15px;display:flex;align-items:center;justify-content:center;letter-spacing:.2px}
.photo{position:absolute}

/* nav */
.site-header{position:absolute;left:0;top:0;width:1200px;height:79px;box-shadow:0 2px 6px rgba(0,0,0,.06);background:var(--white);z-index:2}
.brand{position:absolute;left:66px;top:28px;font-family:"Lexend",sans-serif;font-weight:600;font-size:14px;color:var(--red);display:flex;align-items:center;gap:6px}
.brand i{width:12px;height:12px;background:var(--blue);display:block}
.main-nav{position:absolute;left:282px;top:29px;display:flex;gap:19px;font-family:"Lexend",sans-serif;font-size:15px;text-transform:uppercase;color:#333}

/* hero */
.hero{position:absolute;left:0;top:79px;width:1200px;height:600px;background:linear-gradient(120deg,#F5F8FB,#FFFFFF 60%)}
.hero-title{left:60px;top:272px;font-size:34px;line-height:50px;font-weight:500;color:#1E1E1E}
.hero-sub{left:60px;top:428px;width:460px;font-family:"Lexend",sans-serif;font-size:11px;line-height:20px;text-transform:uppercase;color:#333}

/* about */
.about-title{left:614px;top:888px;font-size:34px;font-weight:500;color:var(--blue-bright)}
.about-lead{left:614px;top:942px;width:520px;font-family:"Lexend",sans-serif;font-size:14px;line-height:22px;text-transform:uppercase;color:#222}
.about-copy{left:614px;top:990px;width:500px;font-size:13.5px;line-height:22.5px;color:var(--muted)}

/* electronic security */
.section-title{left:0;width:1200px;text-align:center;font-size:37px;font-weight:400;color:#333}
.ice-band{left:0;top:1791px;width:1200px;height:275px;background:var(--ice)}
.feature-card{position:absolute;top:1520px;width:333px;height:474px;background:var(--white);box-shadow:0 2px 8px rgba(0,0,0,.05)}
.feature-card .photo{left:0;top:0;width:333px;height:318px}
.feature-card h3{position:absolute;left:17px;top:334px;font-family:"Lexend",sans-serif;font-weight:500;font-size:14px;text-transform:uppercase;color:#222}
.feature-card p{position:absolute;left:17px;top:358px;width:290px;font-size:10.5px;line-height:14.5px;color:#555}
.text-link{position:absolute;font-family:"Lexend",sans-serif;font-size:10px;text-transform:uppercase;color:var(--red);display:flex;align-items:center;gap:6px;white-space:nowrap}

/* connect */
.connect-title{left:0;top:2220px;width:1200px;text-align:center;font-size:37px;line-height:57px;font-weight:500;color:var(--white)}
.connect-sub{left:240px;top:2336px;width:720px;text-align:center;font-size:13px;line-height:22px;color:#E6EEF7}
.service-card{position:absolute;top:2419px;width:235px;height:243px;background:var(--navy-card);color:var(--white);text-align:center}
.service-card .service-icon{position:absolute;left:87px;top:16px}
.service-card h4{position:absolute;left:0;top:118px;width:235px;font-family:"Lexend",sans-serif;font-weight:500;font-size:20px;line-height:28px;text-transform:uppercase}
.service-card p{position:absolute;left:20px;top:172px;width:195px;font-size:10px;line-height:14px;color:#DCE8F5}
.service-card .text-link{color:#E6EEF7;left:0;width:235px;justify-content:center;top:210px}
.dots{position:absolute;display:flex;gap:10px}
.dots span{width:12px;height:12px;border-radius:50%;background:var(--white)}

/* partners */
.partner-row{position:absolute;left:90px;top:2868px;width:1010px;height:40px;display:flex;justify-content:space-between;align-items:center}
.partner{font-family:"Lexend",sans-serif;font-weight:600;font-size:19px;color:#222;display:flex;align-items:center;gap:8px;white-space:nowrap}
.partner i{width:13px;height:13px;background:#222;display:block}
.partner.accent{color:var(--blue-bright)}
.partner.accent i{background:var(--blue-bright);border-radius:50%}
.partner.light{color:#555;font-weight:400;font-size:24px}

/* testimonial */
.testimonial{position:absolute;left:286px;top:2995px;width:626px;height:300px;background:#F6F6F6}
.testimonial .photo{left:24px;top:24px;width:232px;height:252px}
.testimonial blockquote{position:absolute;left:281px;top:68px;width:300px;font-size:13px;line-height:21.5px;color:#444}
.testimonial .name{position:absolute;left:281px;top:202px;font-size:12px;text-transform:uppercase;color:#333}
.testimonial .role{position:absolute;left:281px;top:220px;font-size:10px;color:#888}
.ghost-card{position:absolute;top:3033px;height:250px;background:#F7F7F7;opacity:.6}

/* contact */
.contact-panel{left:69px;top:3452px;width:582px;height:518px;background:var(--panel)}
.contact-title{left:118px;top:3516px;font-size:19px;font-weight:400;color:#333}
.field{position:absolute;background:var(--white);border:1px solid #DADADA;font-size:12px;color:#666;padding:12px 16px}

/* footer */
.site-footer{position:absolute;left:0;top:4054px;width:1200px;height:360px;background:var(--footer);color:#C9D9EC}
.footer-brand{position:absolute;left:0;top:72px;width:1200px;text-align:center;font-family:"Lexend",sans-serif;font-weight:600;font-size:18px;color:var(--white)}
.footer-copy{position:absolute;left:232px;top:156px;width:736px;text-align:center;font-size:13px;line-height:21px}
.social{position:absolute;left:546px;top:252px;display:flex;gap:16px}
.social span{width:18px;height:18px;border-radius:50%;border:2px solid var(--white);display:block}
.footer-rule{position:absolute;left:84px;top:305px;width:1032px;height:1px;background:rgba(255,255,255,.25)}
.legal{position:absolute;left:0;top:330px;width:1200px;text-align:center;font-size:12px}
</style>
</head>
<body>

<header class="site-header">
  <div class="brand"><i></i>Maple Wren Systems</div>
  <nav class="main-nav"><span>Home</span><span>About</span><span>Solutions</span><span>Electronic Security</span><span>Resources</span></nav>
  <div class="btn" style="left:984px;top:21px;width:144px;height:37px;font-size:14px">Contact Us</div>
</header>

<section class="hero"></section>
<h1 class="abs display hero-title">Your trusted partner<br>in advanced security<br>solutions.</h1>
<p class="abs hero-sub">Experience cutting-edge technology designed to protect your world seamless, reliable, and tailored security solutions for every need.</p>
<div class="btn" style="left:60px;top:514px;width:214px;height:45px">Get Started Today</div>
<svg class="abs" style="left:560px;top:165px" width="160" height="115"><path d="M9 108V8H152" fill="none" stroke="var(--red)" stroke-width="5"/></svg>
<div class="photo" role="img" aria-label="Woman using a tablet to control her home security system" style="left:583px;top:185px;width:617px;height:494px;background:linear-gradient(135deg,#6B625A,#3E4756 55%,#8A7C6E)"></div>
<svg class="abs" style="left:1095px;top:574px" width="105" height="105"><path d="M105 0V105H0Z" fill="#EAF6FB"/></svg>

<svg class="abs" style="left:93px;top:808px" width="480" height="575"><path d="M3 0V567H474V200" fill="none" stroke="var(--blue-bright)" stroke-width="5"/></svg>
<div class="photo" role="img" aria-label="Portrait of the company founder in a navy suit and bow tie" style="left:108px;top:766px;width:447px;height:600px;background:linear-gradient(180deg,#FFFFFF 0,#FFFFFF 57px,#5A5D62 57px,#2F3A4C)"></div>
<h2 class="abs display about-title">About Us</h2>
<p class="abs about-lead">I founded Maple Wren Systems to bring together technology and honest, reliable service.</p>
<p class="abs about-copy">Lorem Ipsum Available, But The Majority Have Suffered Alteration In Some Form, By Injected Humour, Or Randomised Words Which Don't Look Even Slightly Believable. If You Are Going To Use A Passage Of Lorem Ipsum, You Need To Be Sure There Isn't Anything Embarrassing Hidden In The Middle Of Text. All The Lorem Ipsum Generators On The Internet Tend To Repeat Predefined Chunks As Necessary, Making This The First True Generator On The Internet. It Uses A Dictionary Of Over 200 Latin Words.</p>
<div class="btn" style="left:614px;top:1172px;width:157px;height:40px">Learn More</div>

<h2 class="abs display section-title" style="top:1438px">Electronic Security</h2>
<div class="abs ice-band"></div>
<article class="feature-card" style="left:72px">
  <div class="photo" role="img" aria-label="Woman using a wall-mounted security keypad" style="background:linear-gradient(135deg,#E9E4DE,#B89F86)"></div>
  <h3>Affordable Security</h3>
  <p>Lorem Ipsum available, but the majority have suffered alteration in some form, by injected humour, or randomised words which don't look even slightly believable. If you are going...</p>
  <span class="text-link" style="left:17px;top:428px">Learn More <svg width="18" height="8"><path d="M0 4H16M12 1L16 4L12 7" fill="none" stroke="currentColor" stroke-width="1.3"/></svg></span>
</article>
<article class="feature-card" style="left:434px">
  <div class="photo" role="img" aria-label="Home theatre room with a large screen" style="background:linear-gradient(160deg,#8A8580,#C9BBA8 60%,#6E655C)"></div>
  <h3>Enviable Entertainment</h3>
  <p>Lorem Ipsum available, but the majority have suffered alteration in some form, by injected humour, or randomised words which don't look even slightly believable. If you are going...</p>
  <span class="text-link" style="left:17px;top:428px">Learn More <svg width="18" height="8"><path d="M0 4H16M12 1L16 4L12 7" fill="none" stroke="currentColor" stroke-width="1.3"/></svg></span>
</article>
<article class="feature-card" style="left:795px">
  <div class="photo" role="img" aria-label="Business team on a video conference call" style="background:linear-gradient(150deg,#DDE3EA,#8C98A8 60%,#4A5566)"></div>
  <h3>Connected Businesses</h3>
  <p>Lorem Ipsum available, but the majority have suffered alteration in some form, by injected humour, or randomised words which don't look even slightly believable. If you are going...</p>
  <span class="text-link" style="left:17px;top:428px">Learn More <svg width="18" height="8"><path d="M0 4H16M12 1L16 4L12 7" fill="none" stroke="currentColor" stroke-width="1.3"/></svg></span>
</article>

<svg class="abs" style="left:0;top:2120px" width="1200" height="660">
  <path d="M0 78L600 22L1200 78V657H0Z" fill="var(--navy)"/>
  <path d="M0 70L593 8M607 8L1200 63" fill="none" stroke="var(--blue-bright)" stroke-width="5"/>
</svg>
<h2 class="abs display connect-title">Effortlessly connect and<br>protect your world</h2>
<p class="abs connect-sub">Lorem Ipsum available, but the majority have suffered alteration in some form, by injected humour, or randomised words which don't look even slightly</p>

<div class="service-card" style="left:89px">
  <svg class="service-icon" width="62" height="76" viewBox="0 0 62 76" fill="none" stroke="#fff" stroke-width="3"><path d="M28 4H54V72H28Z"/><path d="M28 4L44 12V64L28 72"/><path d="M2 38H24M16 30L24 38L16 46"/></svg>
  <h4>Entry &amp; Motion<br>Sensors</h4>
  <p>Lorem Ipsum available, but majority in have suffered alteration...</p>
  <span class="text-link">Learn More <svg width="18" height="8"><path d="M0 4H16M12 1L16 4L12 7" fill="none" stroke="currentColor" stroke-width="1.3"/></svg></span>
</div>
<div class="service-card" style="left:351px">
  <svg class="service-icon" width="62" height="76" viewBox="0 0 62 76" fill="none" stroke="#fff" stroke-width="3"><rect x="2" y="24" width="40" height="30" rx="3"/><path d="M42 34L60 24V54L42 44"/></svg>
  <h4>Video<br>Doorbells</h4>
  <p>Lorem Ipsum available, but majority in have suffered alteration...</p>
  <span class="text-link">Learn More <svg width="18" height="8"><path d="M0 4H16M12 1L16 4L12 7" fill="none" stroke="currentColor" stroke-width="1.3"/></svg></span>
</div>
<div class="service-card" style="left:614px">
  <svg class="service-icon" width="62" height="76" viewBox="0 0 62 76" fill="none" stroke="#fff" stroke-width="3"><path d="M6 30L38 12L52 34L20 52Z"/><path d="M52 34L60 46L44 54"/><path d="M28 48L30 60H14M14 52V68"/></svg>
  <h4>Security<br>Cameras</h4>
  <p>Lorem Ipsum available, but majority in have suffered alteration...</p>
  <span class="text-link">Learn More <svg width="18" height="8"><path d="M0 4H16M12 1L16 4L12 7" fill="none" stroke="currentColor" stroke-width="1.3"/></svg></span>
</div>
<div class="service-card" style="left:876px">
  <svg class="service-icon" width="62" height="76" viewBox="0 0 62 76" fill="none" stroke="#fff" stroke-width="3"><path d="M31 72C16 72 8 62 8 50C8 36 20 30 22 14C30 20 34 28 32 36C38 32 40 26 40 22C50 32 54 42 54 50C54 62 46 72 31 72Z"/><path d="M31 66C25 66 22 62 22 56C22 50 28 46 30 40C36 46 40 52 40 57C40 62 36 66 31 66Z"/></svg>
  <h4>Fire &amp; Carbon<br>Monoxide</h4>
  <p>Lorem Ipsum available, but majority in have suffered alteration...</p>
  <span class="text-link">Learn More <svg width="18" height="8"><path d="M0 4H16M12 1L16 4L12 7" fill="none" stroke="currentColor" stroke-width="1.3"/></svg></span>
</div>
<div class="dots" style="left:549px;top:2702px"><span></span><span></span><span style="background:var(--red)"></span><span></span><span></span></div>

<div class="partner-row">
  <div class="partner"><i></i>Northvale Audio</div>
  <div class="partner">Alertline</div>
  <div class="partner">Doorkin</div>
  <div class="partner">Latchpoint</div>
  <div class="partner accent"><i></i>Meridian</div>
  <div class="partner light">Corvo</div>
</div>

<div class="ghost-card" style="left:0;width:225px"></div>
<div class="ghost-card" style="left:972px;width:228px"></div>
<div class="testimonial">
  <div class="photo" role="img" aria-label="Portrait of the co-owner in a navy suit" style="background:linear-gradient(180deg,#4A5A70,#1F2E4A)"></div>
  <svg class="abs" style="left:570px;top:24px" width="36" height="28" viewBox="0 0 36 28" fill="var(--blue-bright)"><path d="M2 28V16C2 8 6 3 14 1L15 5C10 7 9 10 9 13H15V28ZM21 28V16C21 8 25 3 33 1L34 5C29 7 28 10 28 13H34V28Z"/></svg>
  <blockquote>There are many variations of passages of Lorem Ipsum available, but the majority have suffered alteration in some form, by injected humour, or randomised words which don't look even slightly believable.</blockquote>
  <div class="name">Calder Rusk</div>
  <div class="role">CO-Owner</div>
</div>
<svg class="abs" style="left:480px;top:3340px" width="240" height="24">
  <path d="M12 4L5 12L12 20" fill="none" stroke="var(--red)" stroke-width="3"/>
  <circle cx="55" cy="12" r="6" fill="var(--red)"/>
  <circle cx="81" cy="12" r="5" fill="#E3E3E3"/><circle cx="107" cy="12" r="5" fill="#E3E3E3"/><circle cx="133" cy="12" r="5" fill="#E3E3E3"/><circle cx="159" cy="12" r="5" fill="#E3E3E3"/><circle cx="185" cy="12" r="5" fill="#E3E3E3"/>
  <path d="M228 4L235 12L228 20" fill="none" stroke="var(--red)" stroke-width="3"/>
</svg>

<div class="abs contact-panel"></div>
<h2 class="abs display contact-title">Send us a message</h2>
<div class="field" style="left:118px;top:3567px;width:473px;height:41px">Your Name</div>
<div class="field" style="left:118px;top:3625px;width:232px;height:42px">E-Mail</div>
<div class="field" style="left:360px;top:3625px;width:231px;height:42px">Phone</div>
<div class="field" style="left:118px;top:3684px;width:473px;height:41px">Company</div>
<div class="field" style="left:118px;top:3742px;width:473px;height:110px;padding-top:22px">Type Here</div>
<div class="btn" style="left:118px;top:3874px;width:160px;height:41px">Learn More</div>
<div class="photo" role="img" aria-label="Woman with curly hair talking on a video call at her desk" style="left:651px;top:3452px;width:477px;height:518px;background:linear-gradient(135deg,#5F6B6E,#B7B1A6 55%,#E7E3DC)"></div>

<footer class="site-footer">
  <div class="footer-brand">Maple Wren Systems</div>
  <p class="footer-copy">lorem ipsum is that it has a more-or-less normal distribution of letters, as opposed to using 'content here, content here', making it look like readable english. many desktop publishing packages and web page editors now use lorem ipsum as their default model text, and a search for</p>
  <div class="social" aria-label="Social media links"><span></span><span></span><span></span></div>
  <div class="footer-rule"></div>
  <div class="legal">© 2024 Maple-Wren-Systems</div>
</footer>

</body>
</html>
```